New Business Card Design Project

We require a business card design for Vexalund, a newly established Indian company.
Our focus is on the development, manufacturing, and export of a diverse array of pharmaceutical products on a global scale. The card should convey a professional appearance, as our primary markets are in Africa, China, and Southeast Asian nations.
We envision a two-sided business card, with the reverse side dedicated to a logo set against a solid color or an elegantly designed pattern. The corners should be rounded. We would appreciate seeing both horizontal and vertical design options. We trust the designer to utilize their expertise in creating this design.

The content for the business card is included in the attached Word file.

Target Market(s)

Our primary markets are in Africa, China, and Southeast Asian, Latin America, Maldives, Sri Lanka

Industry/Entity Type

Pharmaceutical Manufacturing and Export

Contact Information for Business Card

Colors

Designer to choose colors to be used in the design.

Requirements
Must have
• The reverse side of the business card features solely the logo along with the tagline, "Remedies of Life."
Should not have
• The logo should not exceed two instances, encompassing both the front and back sides of the card.

```html
<!DOCTYPE html>
<html lang="en">
<head>
<meta charset="utf-8">
<title>Vexalund Business Card</title>
<link href="https://fonts.googleapis.com/css2?family=Poppins:wght@400;500;600;700&display=swap" rel="stylesheet">
<style>
  :root {
    --brand-blue: #29a8e0;
    --brand-coral: #ef5b4b;
    --paper: #ffffff;
    --ink: #333333;
    --stage: #e9ecef;
  }
  * { margin: 0; padding: 0; box-sizing: border-box; }
  html, body { width: 1200px; height: 900px; overflow: hidden; }
  body {
    background: var(--stage);
    font-family: "Poppins", sans-serif;
    position: relative;
  }
  .card {
    position: absolute;
    width: 700px;
    height: 400px;
    left: 250px;
    border-radius: 22px;
    overflow: hidden;
    box-shadow: 0 6px 18px rgba(0,0,0,0.12);
  }
  /* Back side */
  .card-back { top: 36px; background: var(--brand-blue); }
  .back-pattern {
    position: absolute; right: 0; top: 0; width: 240px; height: 400px;
    background: radial-gradient(ellipse at 60% 50%, rgba(255,255,255,0.22), rgba(255,255,255,0) 70%);
  }
  .back-lockup {
    position: absolute; left: 0; right: 0; top: 148px;
    display: flex; flex-direction: column; align-items: center; gap: 14px;
  }
  .back-mark { display: flex; align-items: center; gap: 18px; }
  .back-mark .dot { width: 22px; height: 22px; border-radius: 50%; background: var(--paper); }
  .back-mark .brand-name { color: var(--paper); font-weight: 600; font-size: 62px; line-height: 1; }
  .tagline { color: var(--paper); font-size: 18px; font-weight: 400; letter-spacing: 3px; text-transform: uppercase; }

  /* Front side */
  .card-front { top: 466px; background: var(--paper); }
  .front-waves { position: absolute; inset: 0; }
  .front-mark {
    position: absolute; left: 48px; top: 64px;
    display: flex; align-items: center; gap: 12px;
  }
  .front-mark .dot { width: 18px; height: 18px; border-radius: 50%; background: var(--brand-coral); }
  .front-mark .brand-name { color: var(--brand-blue); font-weight: 600; font-size: 48px; line-height: 1; }
  .holder {
    position: absolute; right: 44px; top: 112px; text-align: right;
  }
  .holder-name { font-weight: 700; font-size: 30px; line-height: 1; letter-spacing: 0.5px; }
  .holder-name .first { color: var(--brand-blue); }
  .holder-name .last { color: var(--brand-coral); }
  .holder-title { color: var(--ink); font-size: 15px; margin-top: 4px; }
  .edge-tab {
    position: absolute; right: 0; top: 118px; width: 14px; height: 40px; background: var(--brand-blue);
  }
  .contact {
    position: absolute; right: 40px; top: 270px; text-align: right; color: var(--paper);
    font-size: 15px; line-height: 22px;
  }
  .contact .row { display: flex; justify-content: flex-end; align-items: center; gap: 8px; }
  .contact svg { width: 13px; height: 13px; flex: none; }
  .contact .address { margin-top: 8px; }
</style>
</head>
<body>

  <section class="card card-back" aria-label="Card reverse side">
    <div class="back-pattern" role="img" aria-label="Soft bubble pattern"></div>
    <div class="back-lockup">
      <div class="back-mark">
        <span class="dot"></span>
        <span class="brand-name">Vexalund</span>
      </div>
      <p class="tagline">Remedies of Life</p>
    </div>
  </section>

  <section class="card card-front" aria-label="Card front side">
    <svg class="front-waves" viewBox="0 0 700 400" preserveAspectRatio="none" aria-hidden="true">
      <path d="M0,205 C160,262 330,242 460,236 C560,231 640,226 700,246 L700,400 L0,400 Z" fill="var(--brand-blue)"/>
      <path d="M0,184 C160,240 330,221 460,215 C560,210 640,206 700,224" fill="none" stroke="var(--brand-coral)" stroke-width="11"/>
      <path d="M0,162 C110,212 250,222 390,223" fill="none" stroke="var(--brand-blue)" stroke-width="7" stroke-linecap="round"/>
    </svg>

    <div class="front-mark">
      <span class="dot"></span>
      <span class="brand-name">Vexalund</span>
    </div>

    <div class="holder">
      <div class="holder-name"><span class="first">DANA</span> <span class="last">MORROW</span></div>
      <div class="holder-title">Founder &amp; Principal</div>
    </div>
    <div class="edge-tab"></div>

    <div class="contact">
      <div class="row">+1- 415-555-0148
        <svg viewBox="0 0 16 16"><path d="M4 1l3 3-2 2c1 2 3 4 5 5l2-2 3 3-2 3C7 15 1 9 1 3z" fill="#fff"/></svg>
      </div>
      <div class="row">info@vexalund.com
        <svg viewBox="0 0 16 16"><rect x="1.5" y="3.5" width="13" height="9" rx="1" fill="none" stroke="#fff" stroke-width="1.6"/><path d="M2 4l6 5 6-5" fill="none" stroke="#fff" stroke-width="1.6"/></svg>
      </div>
      <div class="row">www.vexalund.com
        <svg viewBox="0 0 16 16"><circle cx="8" cy="8" r="6.5" fill="none" stroke="#fff" stroke-width="1.5"/><path d="M1.5 8h13M8 1.5c-3 3.5-3 9.5 0 13M8 1.5c3 3.5 3 9.5 0 13" fill="none" stroke="#fff" stroke-width="1.2"/></svg>
      </div>
      <div class="address">
        <div class="row">4120 North Alder Street</div>
        <div class="row">#27, Suite Fairview Park</div>
      </div>
    </div>
  </section>

</body>
</html>
```